Business Card for Lantern Reach

Please design a Modern Business card for a Online Marketing Company

Website: http://www.lanternreach-example.com.au

Please do NOT include physical address in design.

```html
<!DOCTYPE html>
<html lang="en">
<head>
<meta charset="utf-8">
<title>Lantern Reach – Business Card</title>
<link rel="stylesheet" href="https://fonts.googleapis.com/css2?family=Open+Sans:wght@400;600&family=Roboto:wght@700;900&display=swap">
<style>
  :root {
    --page-bg: #ece9e4;
    --card-dark-centre: #3c4249;
    --card-dark-edge: #1f2226;
    --brand-red: #c30d1c;
    --accent-orange: #f07e1b;
    --text-light: #ffffff;
    --text-muted: #c9ccd0;
    --text-soft: #e3e5e8;
  }
  * { box-sizing: border-box; margin: 0; padding: 0; }
  html, body {
    width: 1200px; height: 470px; overflow: hidden;
    background: var(--page-bg);
  }
  .sheet {
    position: relative; width: 1200px; height: 470px;
    display: flex; align-items: center; justify-content: center; gap: 40px;
  }
  .card {
    position: relative; width: 540px; height: 310px;
    border-radius: 3px; overflow: hidden;
    box-shadow: 0 6px 18px rgba(0,0,0,.25);
  }

  /* Back: contact side */
  .card--back {
    background: radial-gradient(ellipse at 55% 55%, var(--card-dark-centre) 0%, var(--card-dark-edge) 75%);
    font-family: "Open Sans", sans-serif;
  }
  .contact-list {
    position: absolute; top: 26px; right: 26px;
    list-style: none; display: flex; flex-direction: column; gap: 10px;
  }
  .contact-item {
    display: flex; align-items: center; justify-content: flex-end; gap: 12px;
    color: var(--text-soft); font-size: 13px; letter-spacing: .2px;
  }
  .contact-icon {
    width: 30px; height: 30px; border-radius: 3px;
    background: var(--accent-orange);
    display: flex; align-items: center; justify-content: center;
  }
  .contact-icon svg { width: 18px; height: 18px; }
  .holder {
    position: absolute; left: 30px; top: 132px; color: var(--text-light);
  }
  .holder-name { font-size: 21px; font-weight: 600; }
  .holder-title { font-size: 13px; color: var(--text-muted); margin-top: 2px; }
  .brand-block {
    position: absolute; left: 30px; bottom: 30px;
  }
  .brand-row { display: flex; align-items: center; gap: 10px; }
  .brand-square {
    width: 22px; height: 22px; background: var(--brand-red);
  }
  .brand-name {
    font-family: "Roboto", sans-serif; font-weight: 700;
    font-size: 20px; color: var(--brand-red); letter-spacing: .3px;
  }
  .brand-tagline {
    font-family: "Roboto", sans-serif; font-weight: 700;
    font-size: 11px; color: var(--text-light); margin: 4px 0 0 34px;
  }

  /* Front: brand side */
  .card--front {
    background: var(--brand-red); color: var(--text-light);
    display: flex; flex-direction: column; align-items: center; justify-content: center;
    text-align: center;
  }
  .front-name {
    font-family: "Roboto", sans-serif; font-weight: 900;
    font-size: 46px; letter-spacing: .5px; line-height: 1;
  }
  .front-tagline {
    font-family: "Roboto", sans-serif; font-weight: 700;
    font-size: 23px; margin-top: 6px;
  }
  .front-web {
    font-family: "Open Sans", sans-serif; font-size: 19px;
    letter-spacing: .8px; margin-top: 44px;
  }
</style>
</head>
<body>
<main class="sheet">

  <section class="card card--back" aria-label="Business card, contact side">
    <ul class="contact-list">
      <li class="contact-item">0491 570 156
        <span class="contact-icon">
          <svg viewBox="0 0 24 24" fill="#fff" aria-hidden="true"><path d="M6.6 10.8a15.2 15.2 0 0 0 6.6 6.6l2.2-2.2c.3-.3.7-.4 1-.2 1.1.4 2.3.6 3.6.6.6 0 1 .4 1 1V20c0 .6-.4 1-1 1A17 17 0 0 1 3 4c0-.6.4-1 1-1h3.5c.6 0 1 .4 1 1 0 1.3.2 2.5.6 3.6.1.3 0 .7-.2 1z"/></svg>
        </span>
      </li>
      <li class="contact-item">www.lanternreach-example.com.au
        <span class="contact-icon">
          <svg viewBox="0 0 24 24" fill="none" stroke="#fff" stroke-width="1.8" aria-hidden="true"><circle cx="12" cy="12" r="9"/><ellipse cx="12" cy="12" rx="4" ry="9"/><path d="M3 12h18M4.5 7.5h15M4.5 16.5h15"/></svg>
        </span>
      </li>
      <li class="contact-item">plan@lanternreach-example.com.au
        <span class="contact-icon">
          <svg viewBox="0 0 24 24" fill="none" stroke="#fff" stroke-width="1.8" aria-hidden="true"><rect x="3" y="6" width="18" height="12" rx="1"/><path d="M3 6l9 7 9-7"/></svg>
        </span>
      </li>
    </ul>

    <div class="holder">
      <p class="holder-name">Your Name</p>
      <p class="holder-title">Title</p>
    </div>

    <div class="brand-block">
      <div class="brand-row">
        <span class="brand-square" aria-hidden="true"></span>
        <span class="brand-name">LANTERN REACH</span>
      </div>
      <p class="brand-tagline">Get seen online - Grow online</p>
    </div>
  </section>

  <section class="card card--front" aria-label="Business card, brand side">
    <h1 class="front-name">LANTERN REACH</h1>
    <p class="front-tagline">Get seen online - Grow online</p>
    <p class="front-web">www.lanternreach-example.com.au</p>
  </section>

</main>
</body>
</html>
```